Northfield Builders Guild Business card

We are looking for a new business card design with photo included.
Our business is a nonprofit construction contractor membership organization. We offer business education, assist with business setup and licensing, provide safety training, and provide a member directory.
URL: www.builderslinkguild.org
Color code:
CMYK: 0 cyan, 42 magenta, 100 yellow, 0 black for Print.
Hexidecimal: #FF9900
RGB: R 255; G 153; B 0

```html
<!DOCTYPE html>
<html lang="en">
<head>
<meta charset="utf-8">
<title>Northfield Builders Guild – Business Card</title>
<link href="https://fonts.googleapis.com/css2?family=Jost:wght@300;400;600;700&display=swap" rel="stylesheet">
<style>
  :root {
    --stage: #e4e1dc;
    --card-dark: #262626;
    --card-darker: #141414;
    --frost: #dcd8d2;
    --frost-light: #ece9e4;
    --orange: #ff9900;
    --orange-deep: #e8680f;
    --text-light: #eeeeee;
    --ink: #1c1c1c;
  }
  * { margin: 0; padding: 0; box-sizing: border-box; }
  html, body {
    width: 1200px; height: 969px; overflow: hidden;
    background: var(--stage);
    font-family: "Jost", "Futura", sans-serif;
  }
  .business-card {
    position: absolute; left: 100px; top: 199px;
    width: 1000px; height: 571px;
    border-radius: 24px; overflow: hidden;
    box-shadow: 0 14px 40px rgba(0,0,0,.22);
  }
  .card-art { position: absolute; inset: 0; }
  .contact-block { position: absolute; left: 59px; top: 104px; color: var(--text-light); }
  .person-name {
    font-weight: 700; font-size: 33px; letter-spacing: .5px;
    color: var(--orange-deep); line-height: 1;
  }
  .person-title {
    font-weight: 400; font-size: 23px; color: var(--orange-deep);
    margin-top: 10px; line-height: 1;
  }
  .address {
    margin-top: 48px; font-weight: 300; font-size: 23px; line-height: 28px;
  }
  .contact-list { list-style: none; margin-top: 38px; }
  .contact-list li {
    display: flex; align-items: center; gap: 12px;
    font-weight: 300; font-size: 22px; line-height: 29px;
  }
  .contact-list svg { width: 18px; height: 18px; flex: none; fill: var(--orange-deep); }
  .org-name {
    position: absolute; left: 520px; width: 400px; top: 212px;
    text-align: center; color: var(--ink);
    font-weight: 700; font-size: 46px; line-height: 50px; letter-spacing: -.5px;
    text-transform: uppercase;
  }
</style>
</head>
<body>
  <div class="business-card">
    <svg class="card-art" viewBox="0 0 1000 571" width="1000" height="571">
      <defs>
        <linearGradient id="darkPanel" x1="0" y1="0" x2="1" y2="1">
          <stop offset="0" stop-color="var(--card-dark)"/>
          <stop offset="1" stop-color="var(--card-darker)"/>
        </linearGradient>
        <radialGradient id="frostPanel" cx="0.7" cy="0.45" r="0.6">
          <stop offset="0" stop-color="var(--frost-light)"/>
          <stop offset="1" stop-color="var(--frost)"/>
        </radialGradient>
        <linearGradient id="arcStroke" x1="0" y1="0" x2="0" y2="1">
          <stop offset="0" stop-color="var(--orange)"/>
          <stop offset="0.5" stop-color="var(--orange-deep)"/>
          <stop offset="1" stop-color="var(--orange)"/>
        </linearGradient>
      </defs>
      <rect class="dark-panel" width="1000" height="571" fill="url(#darkPanel)"/>
      <path class="frost-panel" d="M644 0 A290 290 0 0 0 644 571 L1000 571 L1000 0 Z" fill="url(#frostPanel)"/>
      <path class="accent-arc" d="M644 0 A290 290 0 0 0 644 571" fill="none" stroke="url(#arcStroke)" stroke-width="6"/>
    </svg>

    <div class="contact-block">
      <p class="person-name">DANIEL HARPER</p>
      <p class="person-title">President</p>
      <p class="address">2400 NW Alder Ridge Rd.,<br>Suite #210<br>Salem, OR 97301</p>
      <ul class="contact-list">
        <li><svg viewBox="0 0 24 24"><path d="M6.6 10.8a15 15 0 0 0 6.6 6.6l2.2-2.2a1 1 0 0 1 1-.25 11.4 11.4 0 0 0 3.6.57 1 1 0 0 1 1 1V20a1 1 0 0 1-1 1A17 17 0 0 1 3 4a1 1 0 0 1 1-1h3.5a1 1 0 0 1 1 1c0 1.25.2 2.45.57 3.57a1 1 0 0 1-.25 1Z"/></svg>(555) 218-4470</li>
        <li><svg viewBox="0 0 24 24"><path d="M7 1h10a2 2 0 0 1 2 2v18a2 2 0 0 1-2 2H7a2 2 0 0 1-2-2V3a2 2 0 0 1 2-2Zm0 3v14h10V4Zm5 15.5a1 1 0 1 0 0 2 1 1 0 0 0 0-2Z"/></svg>555.310.2846</li>
        <li><svg viewBox="0 0 24 24"><path d="M2 5h20v14H2Zm2 2v.5l8 5 8-5V7Zm0 2.8V17h16V9.8l-8 5Z"/></svg>support@nbguild.org</li>
        <li><svg viewBox="0 0 24 24"><path d="M12 2a10 10 0 1 0 0 20 10 10 0 0 0 0-20Zm-1 17.9A8 8 0 0 1 4.2 10L9 14.8v1a2 2 0 0 0 2 2Zm6.9-2.5A2 2 0 0 0 16 16h-1v-3a1 1 0 0 0-1-1H8v-2h2a1 1 0 0 0 1-1V7h2a2 2 0 0 0 2-2v-.4a8 8 0 0 1 2.9 12.8Z"/></svg>builderslinkguild.org</li>
      </ul>
    </div>

    <p class="org-name">Northfield<br>Builders Guild</p>
  </div>
</body>
</html>
```